IV Nutritional Clinic Web Design

We are working with Velqo. They are an IV Nutritional Clinic and in need of a new website design.
Some sites to use for inspiration:
https://brightpathcareco.com
https://www.ourzavrowellness.com
https://www.dewspringlounge.com
https://qvitalsurge.com
https://www.lumo-vital.com/pages/iv-therapy-west-hollywood
https://www.tqoncologyhub.com/cancer-care/iv-drips/
https://dripwellary.com
https://corvinahealthhub.com
Thank you for taking the time to consider designing a website for us. We are web developers based in Stockton, CA, USA. Most of our projects go through the same process. Understanding this process may help you win a project with us. We custom-code all of our websites in-house. We don’t have any requirements as to what tools you use for your design, but we prefer Figma files. For any design that we label as four-stars, we send it to the client for review. The client picks the final design they want us to use. Once we complete this process, we will continue to show additional clients all the four-star sites and purchase them later. Your designs will have multiple chances to sell. For better chances of success, we ask that you follow these guidelines.
IMAGES:
If you use any images or icons in the design, we ask that you have a link to the asset so we can purchase the image/icon. Most of the designs we submit do not have the customer’s images on them unless they have some great images. Be creative; show us the feeling you are trying to portray with your image choices. Use any royalty-free site you choose. We subscribe to Pixvane and mainly use their images, but we can purchase images outside of Pixvane.
PLEASE NOTE: we will not submit designs to clients with watermarks on the images.
FONTS:
We ask that you identify the fonts used in the design. This can be done in a message if you want. We typically use Google Fonts and Pixvane Fonts.
CONTENT:
We're always open to different content and ideas. We often submit designs with stock images so the client can see our vision. We typically take pictures after the website launch to use their images with our vision. Lorem Ipsum is fine for paragraphs, but we ask that you write the headers in correct English. We want to be able to show the vision and identify the sections of the website.
INSPIRATION:
We typically add a couple of links in the brief of websites we like to help you get started in your design.
REVISIONS:
We do not often ask for revisions of the designs unless we see something in the design that may not appeal to the client. If there are slight changes that we want to make, we do that in the development process.
FEEDBACK:
We rarely give feedback on designs during the design process. We are working on many website projects and do not have the time to provide feedback. We usually respond if your request is well thought out and asks specific questions, but a note asking “feedback, please” usually goes unanswered.

```html
<!DOCTYPE html>
<html lang="en">
<head>
<meta charset="utf-8">
<title>Velqo Hydration</title>
<link href="https://fonts.googleapis.com/css2?family=Poppins:wght@400;500;600;700&display=swap" rel="stylesheet">
<style>
:root{
  --navy:#1b2383;
  --green:#6c9b2f;
  --green-light:#a3c77a;
  --sky:#b9dcf3;
  --ink:#333a45;
  --muted:#555c66;
  --footer:#1e1f22;
  --white:#fff;
}
*{box-sizing:border-box;margin:0;padding:0}
html,body{width:1200px;height:5376px;overflow:hidden}
body{font-family:'Poppins',sans-serif;color:var(--ink);background:var(--white);position:relative}
section,header,footer,.topbar{position:relative;width:1200px}
.abs{position:absolute}
.btn{position:absolute;display:flex;align-items:center;justify-content:center;border-radius:30px;font-weight:600;font-size:14px;color:var(--white);background:var(--green);white-space:nowrap}
.btn.outline{background:var(--white);color:var(--navy);border:2px solid var(--navy)}
.btn.outline-grey{background:var(--white);color:var(--ink);border:1.5px solid #777}
.ph{position:absolute;overflow:hidden}
/* top bar */
.topbar{height:52px;background:var(--navy);color:var(--white);font-size:14px;display:flex;align-items:center;justify-content:center;gap:22px}
.topbar span{display:flex;align-items:center;gap:7px}
/* header */
.site-header{height:123px}
.brand{position:absolute;left:143px;top:28px}
.brand .name{font-weight:700;font-size:46px;line-height:1;color:var(--navy);letter-spacing:1px}
.brand .tag{font-size:12px;letter-spacing:9px;color:var(--green);margin-top:2px}
.nav{position:absolute;left:371px;top:52px;display:flex;gap:23px;font-size:13.5px;color:var(--ink);white-space:nowrap}
.nav .active{color:var(--navy);font-weight:500;border-bottom:2px solid var(--navy);padding-bottom:6px}
/* hero */
.hero{height:649px;overflow:hidden}
.hero-photo{left:0;top:0;width:1200px;height:649px;
  background:
    radial-gradient(ellipse 90px 110px at 1005px 150px,#e2b79c 0%,rgba(226,183,156,0) 100%),
    radial-gradient(ellipse 80px 100px at 565px 270px,#c89a82 0%,rgba(200,154,130,0) 100%),
    radial-gradient(ellipse 110px 120px at 555px 240px,#4a3429 0%,rgba(74,52,41,0) 100%),
    radial-gradient(ellipse 60px 40px at 940px 495px,#7fb3e0 0%,rgba(127,179,224,0) 100%),
    radial-gradient(ellipse 60px 40px at 1080px 470px,#7fb3e0 0%,rgba(127,179,224,0) 100%),
    radial-gradient(ellipse 200px 280px at 610px 470px,#f7f7f8 0%,rgba(247,247,248,0) 100%),
    radial-gradient(ellipse 190px 330px at 1010px 420px,#fbfbfc 0%,rgba(251,251,252,0) 100%),
    radial-gradient(ellipse 260px 90px at 1000px 640px,#3a3a3e 0%,rgba(58,58,62,0) 100%),
    linear-gradient(100deg,#e6e6e9 0%,#d6d6d9 40%,#c8c8cc 70%,#bdbdc1 100%)}
.hero h1{position:absolute;left:141px;top:380px;font-size:58px;font-weight:700;color:var(--navy);line-height:1;top:205px;white-space:nowrap}
.hero h1 em{font-style:normal;color:var(--green)}
.hero p{position:absolute;left:145px;top:293px;font-size:20px;font-weight:600;color:#1d1d1d;line-height:1.5}
.dots{position:absolute;left:145px;top:593px;display:flex;gap:8px}
.dots i{display:block;width:26px;height:4px;background:var(--white)}
.dots i:first-child{background:var(--navy)}
/* welcome */
.welcome{height:532px}
.welcome h2{position:absolute;left:614px;top:60px;font-size:38px;font-weight:700;color:var(--navy);line-height:1.1}
.welcome h2 span{display:block;font-weight:400;color:var(--green)}
.welcome .copy{position:absolute;left:614px;top:186px;width:446px;font-size:13px;line-height:22.5px;color:var(--ink)}
.welcome .copy p+p{margin-top:10px}
/* services */
.services{height:940px}
.sec-title{position:absolute;width:100%;text-align:center;font-size:36px;font-weight:700}
.underline{position:absolute;height:2px;background:var(--white)}
.card{position:absolute;background:var(--white);border-radius:12px;box-shadow:0 4px 14px rgba(0,0,0,.15);text-align:center}
.card h3{font-size:19px;font-weight:600;color:var(--navy);margin-top:14px}
.card p{font-size:13px;line-height:24px;color:var(--muted);padding:0 32px;margin-top:6px}
/* testimonials */
.testimonials{height:740px}
.quote{position:absolute;width:443px;height:271px;border-radius:14px;background:rgba(255,255,255,.18);color:var(--white);padding:30px 16px}
.quote p{font-size:16.5px;line-height:32px;width:405px}
.person{display:flex;align-items:center;gap:14px;margin-top:26px}
.avatar{width:56px;height:56px;border-radius:50%;background:var(--white);display:flex;align-items:center;justify-content:center}
.person b{font-size:18px;font-weight:600}
.stars{color:#f6b01e;font-size:15px;letter-spacing:3px}
/* treatments */
.treatments{height:668px}
.treat{position:absolute;width:443px;height:163px;border:2px solid var(--green-light);border-radius:12px;padding:20px 20px 0 110px}
.treat .ico{position:absolute;left:14px;top:30px;width:76px;height:76px;border-radius:50%;display:flex;align-items:center;justify-content:center}
.treat h3{font-size:22px;font-weight:600;color:var(--navy)}
.treat p{font-size:12.5px;line-height:22px;color:var(--muted);margin-top:4px}
/* cta */
.cta{height:460px;overflow:hidden}
.cta h2{position:absolute;width:100%;text-align:center;top:68px;font-size:38px;font-weight:700;color:var(--white)}
.cta p{position:absolute;width:100%;text-align:center;top:145px;font-size:16px;line-height:26px;color:var(--white)}
/* faq */
.faq{height:709px}
.faq h2{position:absolute;left:143px;top:70px;font-size:36px;font-weight:700;color:#3b3f47}
.faq ul{position:absolute;left:143px;top:185px;width:507px;list-style:none}
.faq li{height:56px;border-bottom:1px solid #ddd;display:flex;align-items:center;justify-content:space-between;font-size:14px;color:#444}
.faq li b{font-size:22px;font-weight:600;color:#222}
/* booking band */
.book{height:115px;background:var(--navy)}
.book h2{position:absolute;left:316px;top:35px;font-size:28px;font-weight:600;color:var(--white)}
/* footer */
.site-footer{height:388px;background:var(--footer);color:#ccd;font-size:13px}
.site-footer h4{font-size:17px;font-weight:600;color:var(--white);margin-bottom:14px}
.col{position:absolute;top:52px;line-height:28px}
.fbrand{position:absolute;left:143px;top:130px}
.fbrand .name{font-weight:700;font-size:46px;line-height:1;color:var(--white)}
.fbrand .tag{font-size:12px;letter-spacing:9px;color:var(--white);margin-top:2px}
.social{display:flex;gap:14px;margin-top:6px}
.social i{display:block;width:20px;height:20px;border-radius:50%;background:#d6d8de}
.copyright{position:absolute;left:143px;right:143px;top:330px;border-top:1px solid #3a3b40;padding-top:14px;display:flex;justify-content:space-between;font-size:12px}
.copyright div{display:flex;gap:34px}
</style>
</head>
<body>

<div class="topbar">
  <span><svg width="12" height="14" viewBox="0 0 12 14"><path d="M6 0a5 5 0 0 0-5 5c0 4 5 9 5 9s5-5 5-9a5 5 0 0 0-5-5zm0 7a2 2 0 1 1 0-4 2 2 0 0 1 0 4z" fill="#8bc34a"/></svg>48 Larkmere Lane, Suite 212, Portland 97205, United States</span>
  <span><svg width="13" height="13" viewBox="0 0 13 13"><path d="M3 0l2 3-1.5 1.5a8 8 0 0 0 5 5L10 8l3 2-1.5 3C6 13 0 7 0 1.5z" fill="#8bc34a"/></svg>+1 555-014-2290</span>
  <span><svg width="14" height="11" viewBox="0 0 14 11"><rect width="14" height="11" rx="1" fill="#8bc34a"/><path d="M0 1l7 5 7-5" stroke="#1b2383" fill="none"/></svg>hello@velqoclinic.com</span>
</div>

<header class="site-header">
  <div class="brand"><div class="name">VELQO</div><div class="tag">HYDRATION</div></div>
  <nav class="nav">
    <span class="active">Home</span><span>About</span><span>Services</span><span>Membership</span><span>Blog</span><span>Locations</span><span>Contact Us</span>
  </nav>
  <div class="btn" style="left:933px;top:42px;width:123px;height:40px">Book Now</div>
</header>

<section class="hero">
  <div class="ph hero-photo" role="img" aria-label="Smiling patient in a white robe relaxing during an IV drip beside a confident nurse in a white coat and blue gloves, bright clinic room"></div>
  <h1>Velqo <em>Hydration</em></h1>
  <p>Velqo exceptional infusion therapy services<br>for patients nationwide.</p>
  <div class="btn" style="left:145px;top:375px;width:253px;height:46px">Book An Appointment</div>
  <div class="dots"><i></i><i></i><i></i></div>
</section>

<section class="welcome">
  <div class="ph" role="img" aria-label="Hand holding an IV bag filled with sliced kiwi, orange, grapes and apple" style="left:145px;top:66px;width:444px;height:396px;border-radius:14px;background:
    radial-gradient(circle 55px at 255px 150px,#7fae2e 0%,rgba(127,174,46,0) 100%),
    radial-gradient(circle 50px at 300px 250px,#8cb536 0%,rgba(140,181,54,0) 100%),
    radial-gradient(circle 55px at 310px 120px,#f08a2a 0%,rgba(240,138,42,0) 100%),
    radial-gradient(circle 45px at 190px 240px,#5a2e4a 0%,rgba(90,46,74,0) 100%),
    radial-gradient(circle 60px at 220px 320px,#e8c9a6 0%,rgba(232,201,166,0) 100%),
    radial-gradient(ellipse 130px 190px at 250px 220px,#eef0f4 0%,rgba(238,240,244,0) 100%),
    radial-gradient(ellipse 120px 110px at 400px 360px,#f4f4f6 0%,rgba(244,244,246,0) 100%),
    linear-gradient(135deg,#b9bedc,#9ba2cc 50%,#8890c2)"></div>
  <h2>Welcome to Velqo<span>Hydration</span></h2>
  <div class="copy">
    <p>Nemo enim ipsam voluptatem quia voluptas sit aspernatur aut odit aut fugit, sed quia consequuntur magni dolores eos qui ratione voluptatem sequi nesciunt. Neque porro quisquam est, qui dolorem ipsum quia dolor sit amet, consectetur, adipisci velit, sed quia non numquam eius modi tempora incidunt ut labore et dolore magnam aliquam quaerat voluptatem.</p>
    <p>Nemo enim ipsam voluptatem quia voluptas sit aspernatur aut odit aut fugit, sed quia consequuntur magni dolores eos qui ratione voluptatem sequi nesciunt.</p>
  </div>
  <div class="btn" style="left:614px;top:420px;width:164px;height:40px">Book Now</div>
  <div class="btn outline" style="left:785px;top:420px;width:164px;height:40px">Learn More</div>
</section>

<section class="services">
  <svg class="abs" style="left:0;top:0" width="1200" height="500" viewBox="0 0 1200 500">
    <defs>
      <linearGradient id="svcNavy" x1="0" x2="1"><stop offset="0" stop-color="#1b2383"/><stop offset=".6" stop-color="#1f2a86"/><stop offset="1" stop-color="#202c7a"/></linearGradient>
      <radialGradient id="svcGlow" cx=".8" cy=".35" r=".35"><stop offset="0" stop-color="#3b4a9a" stop-opacity=".7"/><stop offset="1" stop-color="#1b2383" stop-opacity="0"/></radialGradient>
    </defs>
    <path d="M0 100 C250 160 500 120 760 40 C920 -5 1080 0 1200 20 L1200 70 C1050 50 900 70 760 100 C520 150 250 190 0 140Z" fill="#a3c77a"/>
    <path d="M0 120 C250 175 520 140 760 80 C920 45 1080 45 1200 60 L1200 350 C1080 370 960 420 820 440 L380 440 C230 430 120 400 0 350Z" fill="url(#svcNavy)"/>
    <path d="M0 120 C250 175 520 140 760 80 C920 45 1080 45 1200 60 L1200 350 C1080 370 960 420 820 440 L380 440 C230 430 120 400 0 350Z" fill="url(#svcGlow)"/>
    <path d="M820 455 C960 430 1080 380 1200 365" stroke="#a3c77a" stroke-width="10" fill="none"/>
  </svg>
  <h2 class="sec-title" style="top:160px;color:var(--white)">Our Services</h2>
  <div class="underline" style="left:525px;top:222px;width:148px"></div>
  <svg class="abs" style="left:112px;top:495px" width="16" height="30" viewBox="0 0 16 30"><path d="M14 2L2 15l12 13" stroke="#333" stroke-width="2.5" fill="none"/></svg>
  <svg class="abs" style="left:1068px;top:495px" width="16" height="30" viewBox="0 0 16 30"><path d="M2 2l12 13L2 28" stroke="#333" stroke-width="2.5" fill="none"/></svg>

  <div class="card" style="left:146px;top:272px;width:284px;height:484px">
    <div class="ph" role="img" aria-label="Smiling woman beside an IV bag of orange slices" style="left:10px;top:10px;width:264px;height:208px;border-radius:8px;background:
      radial-gradient(ellipse 45px 80px at 40px 110px,#f39a2c 0%,rgba(243,154,44,0) 100%),
      radial-gradient(ellipse 70px 90px at 190px 90px,#8a5a3c 0%,rgba(138,90,60,0) 100%),
      radial-gradient(ellipse 90px 70px at 180px 200px,#d8b05a 0%,rgba(216,176,90,0) 100%),
      linear-gradient(135deg,#f3d9b3,#dcb48a 50%,#b58a62)"></div>
    <div style="height:220px"></div><h3>IV Vitamin Therapy</h3>
    <p>Sed ut perspiciatis unde omnis iste natus errorsit voluptatem ac cusantium doloremque laudantium totam rem aperiam, eaque ipsa quae sint occaec.</p>
    <div class="btn outline-grey" style="left:60px;top:416px;width:164px;height:40px">Book Now</div>
  </div>
  <div class="card" style="left:458px;top:272px;width:284px;height:484px">
    <div class="ph" role="img" aria-label="Clinician performing a body contouring treatment on a patient" style="left:10px;top:10px;width:264px;height:208px;border-radius:8px;background:
      radial-gradient(ellipse 80px 40px at 130px 170px,#3d6fb5 0%,rgba(61,111,181,0) 100%),
      radial-gradient(ellipse 45px 80px at 110px 80px,#5c8f6e 0%,rgba(92,143,110,0) 100%),
      radial-gradient(ellipse 50px 110px at 225px 90px,#1c1f24 0%,rgba(28,31,36,0) 100%),
      linear-gradient(135deg,#dfe3e6,#b9c1c6 55%,#7d868c)"></div>
    <div style="height:220px"></div><h3>Medical Weight Loss</h3>
    <p>Sed ut perspiciatis unde omnis iste natus errorsit voluptatem ac cusantium doloremque laudantium totam rem aperiam, eaque ipsa quae sint occaec.</p>
    <div class="btn outline-grey" style="left:60px;top:416px;width:164px;height:40px">Book Now</div>
  </div>
  <div class="card" style="left:773px;top:272px;width:284px;height:484px">
    <div class="ph" role="img" aria-label="Woman in a spa cap receiving a facial cleansing treatment" style="left:10px;top:10px;width:264px;height:208px;border-radius:8px;background:
      radial-gradient(ellipse 90px 70px at 90px 40px,#ffffff 0%,rgba(255,255,255,0) 100%),
      radial-gradient(ellipse 80px 80px at 110px 130px,#e6c1a8 0%,rgba(230,193,168,0) 100%),
      radial-gradient(ellipse 60px 70px at 210px 110px,#f7f4f1 0%,rgba(247,244,241,0) 100%),
      linear-gradient(135deg,#eef1f4,#dde2e8 55%,#cfd5dd)"></div>
    <div style="height:220px"></div><h3>Anti-Aging Therapies</h3>
    <p>Sed ut perspiciatis unde omnis iste natus errorsit voluptatem ac cusantium doloremque laudantium totam rem aperiam, eaque ipsa quae sint occaec.</p>
    <div class="btn outline-grey" style="left:60px;top:416px;width:164px;height:40px">Book Now</div>
  </div>
  <div class="btn" style="left:502px;top:810px;width:196px;height:42px">See All Services</div>
</section>

<section class="testimonials">
  <svg class="abs" style="left:0;top:0" width="1200" height="740" viewBox="0 0 1200 740">
    <defs><radialGradient id="tGlow" cx=".5" cy=".55" r=".5"><stop offset="0" stop-color="#2c3792"/><stop offset="1" stop-color="#1b2383" stop-opacity="0"/></radialGradient></defs>
    <path d="M0 70 C220 140 480 120 720 50 C900 0 1070 -10 1200 10 L1200 140 L0 140Z" fill="#b9dcf3"/>
    <path d="M0 100 C230 160 500 150 740 80 C920 30 1080 30 1200 50 L1200 740 L0 740Z" fill="#1b2383"/>
    <rect x="0" y="200" width="1200" height="540" fill="url(#tGlow)"/>
  </svg>
  <h2 class="abs" style="left:143px;top:186px;font-size:36px;font-weight:700;color:var(--white)">Client Testimonials</h2>
  <div class="underline" style="left:145px;top:252px;width:148px"></div>
  <svg class="abs" style="left:1000px;top:212px" width="60" height="30" viewBox="0 0 60 30"><path d="M14 3L4 15l10 12" stroke="#fff" stroke-width="2.5" fill="none"/><path d="M44 3l10 12-10 12" stroke="#a3c77a" stroke-width="2.5" fill="none"/></svg>

  <div class="quote" style="left:146px;top:296px">
    <p>“ Neque porro quisquam est, qui dolorem ipsum quia dolor sit amet, consectetur, adipisci velit, sed quia non numquam eius modi te mpora incidunt..”</p>
    <div class="person"><div class="avatar"><svg width="26" height="26" viewBox="0 0 26 26"><circle cx="13" cy="9" r="6" fill="#7fa6d6"/><path d="M2 26c0-7 5-10 11-10s11 3 11 10z" fill="#7fa6d6"/></svg></div><div><b>Dana R</b><div class="stars">★★★★★</div></div></div>
  </div>
  <div class="quote" style="left:612px;top:296px">
    <p>“ Neque porro quisquam est, qui dolorem ipsum quia dolor sit amet, consectetur, adipisci velit, sed quia non numquam eius modi te mpora incidunt..”</p>
    <div class="person"><div class="avatar"><svg width="26" height="26" viewBox="0 0 26 26"><circle cx="13" cy="9" r="6" fill="#7fa6d6"/><path d="M2 26c0-7 5-10 11-10s11 3 11 10z" fill="#7fa6d6"/></svg></div><div><b>Dana R</b><div class="stars">★★★★★</div></div></div>
  </div>
  <div class="btn" style="left:502px;top:618px;width:196px;height:42px">Read All Reviews</div>
</section>

<section class="treatments">
  <h2 class="sec-title" style="top:46px;color:#3b3f47">Our Treatments</h2>
  <div class="treat" style="left:145px;top:160px">
    <div class="ico" style="background:var(--green)"><svg width="40" height="40" viewBox="0 0 40 40" fill="none" stroke="#fff" stroke-width="2"><circle cx="20" cy="14" r="7"/><path d="M8 36c0-8 5-12 12-12s12 4 12 12"/><path d="M30 6c2 3 3 5 3 7a3 3 0 0 1-6 0c0-2 1-4 3-7z"/></svg></div>
    <h3>Dehydration</h3>
    <p>Sed ut perspiciatis unde omnis iste natus errorsit voluptatem accusantium doloremque laudantiumtotam rem aperiam, eaque ipsa quae.</p>
  </div>
  <div class="treat" style="left:612px;top:160px">
    <div class="ico" style="background:var(--navy)"><svg width="40" height="40" viewBox="0 0 40 40" fill="none" stroke="#fff" stroke-width="2"><rect x="11" y="5" width="18" height="22" rx="3"/><path d="M20 27v8M15 12h10M15 18h10"/></svg></div>
    <h3>NAD+ IV Therapy</h3>
    <p>Sed ut perspiciatis unde omnis iste natus errorsit voluptatem accusantium doloremque laudantiumtotam rem aperiam, eaque ipsa quae.</p>
  </div>
  <div class="treat" style="left:145px;top:355px">
    <div class="ico" style="background:var(--navy)"><svg width="40" height="40" viewBox="0 0 40 40" fill="none" stroke="#fff" stroke-width="2"><circle cx="20" cy="20" r="7"/><circle cx="10" cy="10" r="4"/><circle cx="31" cy="29" r="4"/><circle cx="30" cy="10" r="3"/></svg></div>
    <h3>Ozone Therapy</h3>
    <p>Sed ut perspiciatis unde omnis iste natus errorsit voluptatem accusantium doloremque laudantiumtotam rem aperiam, eaque ipsa quae.</p>
  </div>
  <div class="treat" style="left:612px;top:355px">
    <div class="ico" style="background:var(--navy)"><svg width="40" height="40" viewBox="0 0 40 40" fill="none" stroke="#fff" stroke-width="2"><path d="M28 6l6 6M31 9L14 26l-4-4L27 5M12 24l-6 10 10-6"/></svg></div>
    <h3>Micro-Needling</h3>
    <p>Sed ut perspiciatis unde omnis iste natus errorsit voluptatem accusantium doloremque laudantiumtotam rem aperiam, eaque ipsa quae.</p>
  </div>
  <div class="btn" style="left:502px;top:574px;width:196px;height:42px">View All Treatments</div>
</section>

<section class="cta">
  <div class="ph" role="img" aria-label="Relaxed man smiling while receiving IV therapy in a bright clinic lounge with plants" style="left:0;top:0;width:1200px;height:460px;background:
    radial-gradient(ellipse 170px 120px at 500px 330px,#2f6b2a 0%,rgba(47,107,42,0) 100%),
    radial-gradient(ellipse 140px 110px at 180px 370px,#365a22 0%,rgba(54,90,34,0) 100%),
    radial-gradient(ellipse 200px 140px at 1000px 180px,#8bb64a 0%,rgba(139,182,74,0) 100%),
    radial-gradient(ellipse 180px 200px at 80px 140px,#79a83c 0%,rgba(121,168,60,0) 100%),
    linear-gradient(120deg,#5f8f2b,#567f25 50%,#4a7420)"></div>
  <svg class="abs" style="left:0;top:320px" width="1200" height="140" viewBox="0 0 1200 140">
    <path d="M0 20 C200 90 420 120 620 110 C850 95 1050 30 1200 0 L1200 22 C1050 50 850 112 620 122 C420 132 200 108 0 40Z" fill="#1b2383" opacity=".85"/>
    <path d="M0 40 C200 108 420 132 620 122 C850 112 1050 50 1200 22 L1200 140 L0 140Z" fill="#fff"/>
  </svg>
  <h2>Are you ready to elevate you well-being?</h2>
  <p>Take the first step towards enhanced wellness and vitality today by booking your<br>personalized treatment and start feeling your best self</p>
  <div class="btn" style="left:508px;top:222px;width:184px;height:40px;background:var(--navy)">Schedule a Visit</div>
</section>

<section class="faq">
  <h2>FAQ’s</h2>
  <div class="abs" style="left:145px;top:132px;width:148px;height:2px;background:#bbb"></div>
  <ul>
    <li>Sed ut perspiciatis unde omnis iste natus error<b>+</b></li>
    <li>Accusantium doloremque laudantium?<b>+</b></li>
    <li>Aotam rem aperiam, eaque ipsa quae ab illo invento?<b>+</b></li>
    <li>Beatae vitae dicta sunt explicabo?<b>+</b></li>
    <li>Nemo enim ipsam voluptatem quia voluptas.?<b>+</b></li>
    <li>Accusantium doloremque laudantium?<b>+</b></li>
    <li>Aotam rem aperiam, eaque ipsa quae ab illo inventore?<b>+</b></li>
  </ul>
  <div class="btn" style="left:145px;top:604px;width:196px;height:42px">See all FAQ’s</div>
  <div class="ph" role="img" aria-label="Gloved hand holding an IV bag filled with orange, kiwi, grapes and berries" style="left:701px;top:85px;width:355px;height:551px;background:
    radial-gradient(circle 60px at 150px 270px,#f28a1e 0%,rgba(242,138,30,0) 100%),
    radial-gradient(circle 55px at 200px 380px,#7aa62a 0%,rgba(122,166,42,0) 100%),
    radial-gradient(circle 55px at 130px 360px,#4a2a55 0%,rgba(74,42,85,0) 100%),
    radial-gradient(circle 55px at 180px 450px,#c2386a 0%,rgba(194,56,106,0) 100%),
    radial-gradient(ellipse 150px 110px at 200px 80px,#f1eeea 0%,rgba(241,238,234,0) 100%),
    radial-gradient(ellipse 130px 230px at 175px 360px,#e9ecf2 0%,rgba(233,236,242,0) 100%),
    linear-gradient(170deg,#a98b78,#8b7466 35%,#6d7aa8 80%,#5f6ea3)"></div>
</section>

<section class="book">
  <h2>Book Your Appointment</h2>
  <div class="btn" style="left:726px;top:36px;width:158px;height:44px">Book Now</div>
</section>

<footer class="site-footer">
  <div class="fbrand"><div class="name">VELQO</div><div class="tag">HYDRATION</div></div>
  <div class="col" style="left:384px">
    <h4>Navigations</h4>
    Home<br>About<br>Services<br>Membership<br>Blog<br>Locations<br>Contact Us
  </div>
  <div class="col" style="left:611px;width:240px">
    <h4>Contact Us</h4>
    <div style="line-height:24px">48 Larkmere Lane, Suite 212,<br>Portland 97205, US</div>
    <div style="margin-top:6px">+1 555-014-2290</div>
    <div style="margin-top:6px">hello@velqoclinic.com</div>
  </div>
  <div class="col" style="left:887px;width:200px">
    <h4>Hours</h4>
    <div style="display:flex;justify-content:space-between">Mon – Sat<span>8am to 6pm</span></div>
    <div style="display:flex;justify-content:space-between">Sunday –<span style="margin-right:38px">Closed</span></div>
    <h4 style="margin-top:22px;margin-bottom:8px">Follow Us</h4>
    <div class="social"><i></i><i style="background:var(--green)"></i><i></i><i></i><i></i></div>
  </div>
  <div class="copyright">
    <span>Copyright © 2025 Velqo - All Rights Reserved</span>
    <div><span>Privacy Policy</span><span>Terms Of Services</span><span>Disclaimer</span></div>
  </div>
</footer>

</body>
</html>
```